Welcome Center Signage/logo Design with Multicultural Relevance

We are looking to have a welcome signage/logo designed for our church lobby with either the word "welcome" or "Welcome to the Maplecrest FSW Church!"

This design must include our organizational logo (attached). It could (but does not need to) also include our church vision: "Our vision is to be a thriving diverse urban church sharing Christ's love and serving the needs of our local and global communities." The logo/signage will be printed on 4' x 6' stretch fabric.

This signage will then be hung up behind our welcome center...it will be one of the first things people see upon entering our building.

We are an urban multicultural church that has significant outreach into our local community, one that is quite culturally diverse. If you would like more information about our church, please visit www.maplecrestfsw.org.
Updates

Project Deadline Extended
Reason: We have committed to continue work with the designers on designs submitted over the last several days, and are scheduling the additional time needed to do so. Thank you!

Target Market(s)

Culturally (African American, Hispanic American, Asian American, European American) diverse millennials and iGens

Industry/Entity Type

Church

Font styles to use
Sans Serif

Requirements
Must have
• Our logo
Nice to have
• "Welcome" in many languages
Should not have
• I can't think of anything at the moment.

```html
<!DOCTYPE html>
<html lang="en">
<head>
<meta charset="utf-8">
<title>Welcome Center Sign – Maplecrest FSW Church</title>
<link rel="stylesheet" href="https://fonts.googleapis.com/css2?family=Roboto:wght@400;700&family=Noto+Sans+TC:wght@400&display=swap">
<style>
  :root {
    --backdrop: #e6e4df;
    --banner-navy: #1b2e4a;
    --welcome-gold: #e9b43c;
    --mark-red: #c0262d;
    --mark-fill: #6a3a3f;
  }
  * { margin: 0; padding: 0; box-sizing: border-box; }
  html, body {
    width: 1200px;
    height: 750px;
    overflow: hidden;
    background: var(--backdrop);
  }
  .canvas {
    position: relative;
    width: 1200px;
    height: 750px;
    display: flex;
    align-items: center;
    justify-content: center;
  }
  .welcome-banner {
    width: 1050px;
    height: 700px;
    background: var(--banner-navy);
    display: flex;
    flex-direction: column;
    align-items: center;
    font-family: "Roboto", Arial, sans-serif;
    color: var(--welcome-gold);
  }
  .church-identity {
    margin-top: 40px;
    display: flex;
    flex-direction: column;
    align-items: center;
    gap: 26px;
  }
  .identity-circle {
    width: 250px;
    height: 250px;
    border-radius: 50%;
    background: var(--mark-fill);
    border: 6px solid var(--mark-red);
  }
  .church-name {
    font-weight: 700;
    font-size: 40px;
    letter-spacing: 0.5px;
    color: var(--welcome-gold);
  }
  .greetings {
    margin-top: 44px;
    text-align: center;
  }
  .greeting-line {
    font-weight: 700;
    font-size: 50px;
    line-height: 1.0;
  }
  .greeting-line + .greeting-line {
    margin-top: 36px;
  }
  .greeting-chinese {
    margin-top: 12px;
    font-family: "Noto Sans TC", sans-serif;
    font-weight: 400;
    font-size: 42px;
    line-height: 1.0;
  }
</style>
</head>
<body>
  <main class="canvas">
    <section class="welcome-banner">
      <div class="church-identity">
        <div class="identity-circle"></div>
        <p class="church-name">Maplecrest FSW Church</p>
      </div>
      <div class="greetings">
        <p class="greeting-line">Welcome! Bienvenido! Välkommen!</p>
        <p class="greeting-line">Herzlich Willkommen!</p>
        <p class="greeting-chinese" lang="zh-Hant">歡迎！</p>
      </div>
    </section>
  </main>
</body>
</html>
```